Printing Company needs Website

PLEASE REVIEW ALL IMAGES, I HAVE INCLUDED A WEBSITE MOCKUP IDEA AND LOGO FILES IN THESE IMAGES.

Vel-Marks Provides printing services to multiple businesses. We Focus on 4 main markets. Signage (Signs, Banners, Wraps, Custom graphics), Printing (flyers, brochures, business cards, Postcards), Apparel (printed shirts, hoodies, sweatshirts), Promotional Products (mugs, golf balls, brava cans, pens), We try to sell ourselves on total brand imaging, our slogan is "Mark Everything." because we want to be able to provide any type of printing to our customers. Consumer targeting should be targeted towards small business, and wholesale targeting should be geared toward, merchandising, branding, marketing, design, signage, apparel, embroidery, and printing groups. WE DO OFFER DESIGN SERVICES, I have attached one orlwick guild logo design as an example.

I need a website designed both for wholesale and consumer based people. Wholesale customers would have their own login and consumers would also have their own.
I need there to be an online designer software (possibly java) built in so that the customer can order their product or upload their artwork online to see the proof for approval. There will need to be an commence setup, and I do have a quillpay account if that helps. Shipping must be auto calculated at the time of ordering. I would Like to make it to where when customer orders a product if it is outside of the dimensions requested on the site that the customer is warned of clipping or skewing.

I will be working closely aside the designer I pick to aid in the uploading and configuration of pricing structure, weight, and imagery if selected. This will be a lengthy project, and I will be willing to pay for the additional help so long as you are completely aware of the needs, Happy designing!!
Updates

I love all of the designs so far everyone! I will be reviewing PLEASE NOTE, IF I APPROVE YOUR WEB DESIGN, I WILL WANT YOU TO COMPLETE THE ENTIRE DESIGN INCLUDING A DESIGN PROOFING SETUP FOR MY CUSTOMERS INTEGRATED IN AS I HAVE STATED IN THE ORIGINAL STATEMENT. PLEASE ASK QUESTIONS IF YOU DON'T UNDERSTAND!

Target Market(s)

Small Business, School Athletics, Merchandising groups, Branding Groups, Larger Printers, Sign makers, Embroidery shops, Screen Printing Shops

Industry/Entity Type

It Company

Font styles to use
Sans Serif

Colors
000000
1b1b1b
757575
ec1f27

Requirements
Must have
• Built in design setup to each product with sizing, Ability to add pre-designed templates, .pdf print ready files after upload, Wholesale account, or Business accounts all with different pricing structures, Must be willing to aid in setup of all products and services (willing pay additional for setup costs.)
Nice to have
• SEO Optimization, targeting specific groups listed, automatic ordering to outsource vendors straight from site listing drop ship location if need be.

```html
<!DOCTYPE html>
<html lang="en">
<head>
<meta charset="utf-8">
<title>Vel-Marks — Mark Everything.</title>
<link rel="stylesheet" href="https://fonts.googleapis.com/css2?family=Raleway:wght@400;500&family=Open+Sans:ital,wght@0,400;0,600;0,700;1,400&display=swap">
<style>
:root{
  --black:#000000;
  --panel:#1b1b1b;
  --section:#0f0f0f;
  --card:#141414;
  --grey:#757575;
  --light:#bdbdbd;
  --red:#ec1f27;
  --red-dark:#c4151c;
  --white:#ffffff;
}
*{margin:0;padding:0;box-sizing:border-box}
html,body{width:788px;height:1200px;overflow:hidden;background:var(--black)}
body{position:relative;font-family:"Open Sans",Arial,sans-serif;color:var(--white)}
.abs{position:absolute}

/* header */
.site-header{left:0;top:0;width:788px;height:73px;background:var(--black)}
.call{left:108px;top:27px;display:flex;gap:8px;align-items:flex-start}
.call-text{color:var(--red);line-height:1.2}
.call-label{font-size:6.5px;letter-spacing:.2px}
.call-number{font-size:10px;letter-spacing:.8px;margin-top:3px}
.brand{left:0;width:788px;top:20px;display:flex;justify-content:center}
.brand-lockup{display:flex;align-items:center;gap:6px}
.brand-dot{width:14px;height:14px;border-radius:50%;background:var(--red)}
.brand-name{font-family:"Open Sans",sans-serif;font-weight:700;font-size:22px;color:var(--white);letter-spacing:.3px}
.brand-tag{font-size:6px;color:var(--light);text-align:right;margin-top:1px}
.social{left:643px;top:34px;display:flex;gap:7px}
.social span{width:8px;height:8px;border-radius:50%;background:#cfcfcf;display:block}

/* nav */
.main-nav{left:0;top:73px;width:788px;height:32px;background:var(--red)}
.main-nav a{position:absolute;top:0;height:32px;line-height:32px;font-size:7.6px;color:var(--white);text-decoration:none;transform:translateX(-50%);white-space:nowrap}
.main-nav a.active{background:var(--red-dark);width:53px;text-align:center;transform:none;left:106px}

/* hero */
.hero{left:0;top:105px;width:788px;height:381px;background:linear-gradient(100deg,#3a3a3a 0%,#5d5c5a 35%,#6b6a67 60%,#4a4947 100%)}
.hero-title{left:0;width:788px;top:180px;text-align:center;font-family:"Raleway",sans-serif;font-weight:500;font-size:33px;letter-spacing:3px}
.hero-arrow{top:179px;width:23px;height:23px;border:1.5px solid var(--white);border-radius:50%}
.hero-arrow svg{display:block;margin:4px auto}

/* markets */
.markets{left:0;top:486px;width:788px;height:312px;background:var(--section)}
.section-title{left:0;width:788px;text-align:center;font-family:"Raleway",sans-serif;font-size:20.5px;color:var(--white)}
.section-sub{left:0;width:788px;text-align:center;font-size:6.5px;font-style:italic;color:var(--grey)}
.market-card{top:88px;width:133px;height:171px;background:var(--card);border:1px solid #222}
.market-photo{height:85px;width:100%}
.market-name{margin:10px 0 0 10px;font-family:"Raleway",sans-serif;font-size:11px;color:var(--red)}
.market-list{list-style:none;margin:9px 0 0 10px;font-size:6.6px;color:var(--grey);line-height:12px}

/* testimonials */
.testimonials{left:0;top:798px;width:788px;height:226px;background:var(--black)}
.avatar{left:108px;top:94px;width:84px;height:84px;border-radius:50%;border:3px solid #e8e8e8;background:linear-gradient(160deg,#c49a74,#8a5f3f)}
.quote{left:204px;top:92px;width:482px;font-size:7.6px;font-style:italic;line-height:15px;color:var(--light)}
.quote-mark{font-style:normal;font-weight:700;font-size:13px;color:var(--white);line-height:0}
.author{left:204px;top:161px;font-family:"Raleway",sans-serif;font-size:9.5px;color:var(--white)}
.chev{top:120px}

/* footer */
.site-footer{left:0;top:1024px;width:788px;height:176px;background:var(--panel)}
.foot-brand{left:106px;top:57px;display:flex;align-items:center;gap:5px}
.foot-brand .brand-dot{width:11px;height:11px}
.foot-brand .brand-name{font-size:17px}
.copyright{left:106px;top:103px;font-size:6.8px;color:var(--white)}
.foot-col h4{font-family:"Raleway",sans-serif;font-weight:500;font-size:10px;color:var(--white);margin-bottom:9px}
.foot-col ul{list-style:none;font-size:6.8px;color:var(--light);line-height:13.8px}
.foot-col p{font-size:6.8px;font-style:italic;color:var(--light);line-height:12.5px;width:140px}
.signup{left:550px;top:94px;width:134px;height:25px;display:flex;border:1px solid #8a8a8a;background:var(--black)}
.signup span{flex:1;font-size:6.8px;font-style:italic;padding:8px 0 0 8px;color:var(--light)}
.signup b{width:47px;background:var(--red);font-size:7px;font-weight:600;text-align:center;line-height:23px}
.live-chat{left:762px;top:1069px;width:26px;height:72px;background:var(--red);border:1.5px solid var(--white);border-right:0}
.live-chat span{position:absolute;left:50%;top:50%;transform:translate(-50%,-50%) rotate(-90deg);white-space:nowrap;font-size:8px;font-weight:700;letter-spacing:.3px;padding-left:10px}
.live-chat i{position:absolute;left:8px;bottom:6px;width:8px;height:8px;border-radius:50%;background:var(--white)}
</style>
</head>
<body>

<header class="abs site-header">
  <div class="abs call">
    <svg width="14" height="14" viewBox="0 0 24 24"><path d="M6.6 10.8a15 15 0 0 0 6.6 6.6l2.2-2.2a1 1 0 0 1 1-.25 11 11 0 0 0 3.6.6 1 1 0 0 1 1 1V20a1 1 0 0 1-1 1A17 17 0 0 1 3 4a1 1 0 0 1 1-1h3.5a1 1 0 0 1 1 1 11 11 0 0 0 .6 3.6 1 1 0 0 1-.25 1z" fill="none" stroke="#ec1f27" stroke-width="1.6"/></svg>
    <div class="call-text">
      <div class="call-label">Calls Answered in 2 Seconds:</div>
      <div class="call-number">020 4177 5300</div>
    </div>
  </div>
  <div class="abs brand">
    <div>
      <div class="brand-lockup"><span class="brand-dot"></span><span class="brand-name">Vel-Marks</span></div>
      <div class="brand-tag">Mark Everything.</div>
    </div>
  </div>
  <div class="abs social" aria-label="Social links"><span></span><span></span><span></span></div>
</header>

<nav class="abs main-nav">
  <a class="active" href="#">HOME</a>
  <a href="#" style="left:197px">SIGNAGE</a>
  <a href="#" style="left:268px">PRINTING</a>
  <a href="#" style="left:338px">DESIGN</a>
  <a href="#" style="left:416px">PROMOTIONAL</a>
  <a href="#" style="left:498px">APPAREL</a>
  <a href="#" style="left:570px">ABOUT US</a>
  <a href="#" style="left:649px">CONTACT US</a>
</nav>

<section class="abs hero" role="img" aria-label="Office wall wrapped in a printed concrete graphic with a quotation and technical drawing lines">
  <div class="abs hero-title">MARK EVERYTHING</div>
  <div class="abs hero-arrow" style="left:30px"><svg width="12" height="12" viewBox="0 0 12 12"><path d="M7.5 2 3.5 6l4 4" fill="none" stroke="#fff" stroke-width="1.6"/></svg></div>
  <div class="abs hero-arrow" style="left:729px"><svg width="12" height="12" viewBox="0 0 12 12"><path d="M4.5 2l4 4-4 4" fill="none" stroke="#fff" stroke-width="1.6"/></svg></div>
</section>

<section class="abs markets">
  <h2 class="abs section-title" style="top:34px">Our Main Markets</h2>
  <p class="abs section-sub" style="top:62px">Vel-Marks Provides printing services to multiple businesses</p>

  <article class="abs market-card" style="left:106px">
    <div class="market-photo" role="img" aria-label="Hanging sign on a brick wall" style="background:linear-gradient(90deg,#8b4a32,#e6edf0 45%,#a3553a)"></div>
    <h3 class="market-name">Signage</h3>
    <ul class="market-list"><li>Signs</li><li>Banners</li><li>Wraps</li><li>Custom graphics</li></ul>
  </article>
  <article class="abs market-card" style="left:254px">
    <div class="market-photo" role="img" aria-label="Printed memorial panel with flowers" style="background:linear-gradient(90deg,#d9d5cf,#7b5a44 45%,#cfc9c0)"></div>
    <h3 class="market-name">Printing</h3>
    <ul class="market-list"><li>Flyers</li><li>Brochures</li><li>Business Cards</li><li>Postcards</li></ul>
  </article>
  <article class="abs market-card" style="left:402px">
    <div class="market-photo" role="img" aria-label="Printed garment hung on a wall" style="background:linear-gradient(180deg,#e6e3df,#3a9fb0 50%,#d8d4cf)"></div>
    <h3 class="market-name">Apparel</h3>
    <ul class="market-list"><li>Printed shirts</li><li>Hoodies</li><li>Sweatshirts</li></ul>
  </article>
  <article class="abs market-card" style="left:550px">
    <div class="market-photo" role="img" aria-label="Banners on a fence along a grass field" style="background:linear-gradient(180deg,#b9c9d8,#8a8c86 35%,#5d7a3a 60%,#4c6a2e)"></div>
    <h3 class="market-name">Promotional Products</h3>
    <ul class="market-list"><li>Mugs</li><li>Golf balls</li><li>Brava cans</li><li>Pens</li></ul>
  </article>
</section>

<section class="abs testimonials">
  <h2 class="abs section-title" style="top:40px">Client Testimonials</h2>
  <svg class="abs chev" style="left:66px" width="16" height="32" viewBox="0 0 16 32"><path d="M13 2 3 16l10 14" fill="none" stroke="#fff" stroke-width="1.4"/></svg>
  <svg class="abs chev" style="left:708px" width="16" height="32" viewBox="0 0 16 32"><path d="M3 2l10 14L3 30" fill="none" stroke="#fff" stroke-width="1.4"/></svg>
  <div class="abs avatar" role="img" aria-label="Portrait of the client"></div>
  <p class="abs quote"><span class="quote-mark">&ldquo;</span> Sed ut perspiciatis unde omnis iste nater ror sit voptaaccusantium dolorque laudantiumotam rem aperiad perspiciatis unde omnis iste nater ror sit voluptatem accs antium dolorque laudantium, totam rem aperiamedut perspiciatis unde omnis iste ut perspiciatis unde lrom nis iste nater ror sit voptaaccusantium dolorque laudantium, totam rem aperiad perspiciatis unde omnis iste nater ror sit voluptatem ccs antium dolorque laudantium, totam rem aperiamedut peciatis unde omnis iste nater. <span class="quote-mark">&rdquo;</span></p>
  <div class="abs author">Dara Penwell, City Name</div>
</section>

<footer class="abs site-footer">
  <div class="abs foot-brand"><span class="brand-dot"></span><span class="brand-name">Vel-Marks</span></div>
  <div class="abs copyright">© 2016 All Rights are Reserved.</div>

  <div class="abs foot-col" style="left:232px;top:44px">
    <h4>About Us</h4>
    <ul><li>Sed ut perspiciatis</li><li>Qnde omnis iste n</li><li>Wtus error sit voluptat</li><li>em accusantiu</li><li>Gdoloremque</li></ul>
  </div>
  <div class="abs foot-col" style="left:335px;top:44px">
    <h4>Links</h4>
    <ul><li>Sed ut perspicia</li><li>Qnde omnis ist</li><li>Wtus error sit vol</li><li>em accusantiu</li><li>Gdoloremque</li></ul>
  </div>
  <div class="abs foot-col" style="left:435px;top:44px">
    <h4>Contact Us</h4>
    <ul><li>Our Address USA lrem 897</li><li>lorem sipsum dolor 0823.</li><li>Lorem ipsum.</li><li>Phone: 020 6391 2840</li><li>hello@velmarks-mail.com</li></ul>
  </div>
  <div class="abs foot-col" style="left:550px;top:44px">
    <h4>Newsletter</h4>
    <p>Sed ut perspiciatis unde omnis iste nater ror sit voptaaccusantium dolorque lau</p>
  </div>
  <div class="abs signup"><span>Email address</span><b>SIGN UP</b></div>
</footer>

<div class="abs live-chat"><span>LIVE CHAT</span><i></i></div>

</body>
</html>
```